Packaging design for a reclosable bag for our product

We have a logo, and we need to put it on packaging for our product and while we want the look to be simple, we want it to follow good design principles and also contain spaces for other product descriptions.

There will be 5 sizes at launch so I'd like 5 variations, one for each size.

I've included a few mockups of the type of bag that I made but they are all just rough ideas that I had.

I want the brand to look scientific and methodical and even a bit quirky, as in "wow this is a serious product but also a bit unusual."

```html
<!DOCTYPE html>
<html lang="en">
<head>
<meta charset="utf-8">
<title>NV4 Bias Lighting – Pouch Front</title>
<link rel="stylesheet" href="https://fonts.googleapis.com/css2?family=Oswald:wght@500;600&family=Lato:wght@400&display=swap">
<style>
  :root {
    --backdrop: #cbcbcb;
    --pouch: #121212;
    --pouch-edge: #1c1c1c;
    --ink-light: #ffffff;
    --ink-dark: #161616;
    --divider: #e6e6e6;
    --label: #e8e8e8;
  }
  * { margin: 0; padding: 0; box-sizing: border-box; }
  html, body { width: 1200px; height: 1200px; overflow: hidden; background: var(--backdrop); }
  .canvas { position: relative; width: 1200px; height: 1200px; background: var(--backdrop); }

  .pouch-front {
    position: absolute; left: 290px; top: 198px; width: 620px; height: 842px;
    background: radial-gradient(ellipse at 50% 40%, var(--pouch-edge), var(--pouch) 70%);
  }
  .zip-line { position: absolute; left: 0; right: 0; top: 36px; height: 2px; background: #2a2a2a; }
  .tear-notch { position: absolute; top: 14px; width: 10px; height: 2px; background: var(--ink-light); }
  .tear-notch.left { left: -10px; } .tear-notch.right { right: -10px; }

  .brand-name {
    position: absolute; left: 0; right: 0; top: 138px; text-align: center;
    font-family: "Oswald", sans-serif; font-weight: 600; font-size: 118px; line-height: 1;
    color: var(--ink-light); letter-spacing: 2px;
  }
  .product-band {
    position: absolute; left: 0; right: 0; top: 268px; height: 64px;
    background: linear-gradient(90deg, #2a2a2a 0%, #9a9a9a 18%, #ffffff 40%, #ffffff 60%, #9a9a9a 82%, #2a2a2a 100%);
    display: flex; align-items: center; justify-content: center;
    font-family: "Oswald", sans-serif; font-weight: 500; font-size: 50px;
    color: var(--ink-dark); letter-spacing: 1px;
  }
  .screen-visual {
    position: absolute; left: 126px; top: 400px; width: 372px; height: 236px;
    background: #0d0d0d; border-radius: 4px;
    box-shadow: 0 0 40px 14px rgba(255,255,255,0.28), 0 0 90px 30px rgba(255,255,255,0.08);
  }

  .spec-row {
    position: absolute; left: 0; right: 0; top: 662px;
    display: flex; justify-content: center; align-items: stretch;
  }
  .spec { display: flex; flex-direction: column; align-items: center; padding: 0 10px; height: 70px; justify-content: flex-start; }
  .spec + .spec { border-left: 1.5px solid var(--divider); }
  .spec svg { height: 40px; margin-bottom: 6px; }
  .spec-label { font-family: "Lato", sans-serif; font-size: 13px; color: var(--label); white-space: nowrap; }
</style>
</head>
<body>
<div class="canvas">
  <div class="pouch-front">
    <div class="zip-line"></div>
    <span class="tear-notch left"></span><span class="tear-notch right"></span>

    <div class="brand-name">NV4</div>
    <div class="product-band">BIAS LIGHTING</div>
    <div class="screen-visual" role="img" aria-label="Screen silhouette with soft white bias light glowing behind it"></div>

    <div class="spec-row">
      <div class="spec">
        <svg viewBox="0 0 60 40" width="60" fill="none" stroke="#fff" stroke-width="2">
          <rect x="8" y="12" width="44" height="14"/><rect x="12" y="16" width="36" height="6" fill="#fff"/>
          <path d="M12 30l-3 5M22 30l-1 5M30 30v5M38 30l1 5M48 30l3 5"/>
        </svg>
        <span class="spec-label">6500K White</span>
      </div>
      <div class="spec">
        <svg viewBox="0 0 44 40" width="44" fill="none" stroke="#fff" stroke-width="1.5">
          <circle cx="22" cy="20" r="10"/>
          <path d="M22 3v5M22 32v5M5 20h5M34 20h5M10 8l3 3M31 29l3 3M34 8l-3 3M13 29l-3 3"/>
        </svg>
        <span class="spec-label">Simulated</span>
      </div>
      <div class="spec">
        <svg viewBox="0 0 40 40" width="40">
          <circle cx="20" cy="20" r="17" fill="none" stroke="#fff" stroke-width="6" stroke-dasharray="5 2"/>
          <circle cx="20" cy="20" r="10" fill="#fff"/>
        </svg>
        <span class="spec-label">90+</span>
      </div>
      <div class="spec">
        <svg viewBox="0 0 60 40" width="60" fill="none" stroke="#fff" stroke-width="1.5">
          <circle cx="30" cy="19" r="17"/><circle cx="30" cy="19" r="12"/><circle cx="30" cy="19" r="7"/><circle cx="30" cy="19" r="3"/>
          <path d="M30 36h26"/>
        </svg>
        <span class="spec-label">Cable Length 5m</span>
      </div>
      <div class="spec">
        <svg viewBox="0 0 44 40" width="44" fill="none" stroke="#fff" stroke-width="2">
          <path d="M8 12a20 20 0 0 1 28 0M13 17a13 13 0 0 1 18 0M18 22a6 6 0 0 1 8 0"/>
          <rect x="18" y="26" width="8" height="13" fill="#fff" stroke="none"/>
        </svg>
        <span class="spec-label">Wireless Control</span>
      </div>
    </div>
  </div>
</div>
</body>
</html>
```